redesign my website bluekeelvoyages.net and make it user friendly

I already have a website, bluekeelvoyages.net, and want a redesign in WordPress with Elementor Pro, using the same text/content. The goal is to improve:

Design quality (colors, fonts, spacing, visual flow)
User experience (easy navigation, clear offers)
Conversion readiness (calls-to-action, trust signals, booking flow)
Technical side (SEO basics, fast speed, full mobile responsiveness)

The site should look modern, clean, fun, engaging, interactive and optimized for speed and usability.

I would like the 11 page to be consolidate dto 6 as follows: Home (main landing, highlights)

Sailboat Trips (all packages, itineraries, pricing)
Boats (fleet details, features, photos)
How It Works (booking process, FAQs, travel info, what to expect)
Blog
Contact Us (form, WhatsApp, phone, etc.)

Target Market(s)

sailboat trip customers for San Blas Islands in Panama

Industry/Entity Type

Travel, Boat Tour Agency

Coding

Coded - Design and coding required

Number of Pages Required

3 page

Font styles to use
Sans Serif
Other font styles liked:
• Oswalg and sans serif

Colors
0054AA
0677BA
7BADD7
CADEEF
E8F1F8
0094D4
00A9DD
6FCCEA
C7EBF8
E9F6FB
FFC000
F8CF3A
FAE287
FDF2CF
FEFAEE
F0912C
F2A743
F7CA91
FBE8D2
FDF5EE

Requirements
Must have
• Home (main landing, highlights) Sailboat Trips (all packages, itineraries, pricing) Boats (fleet details, features, photos) How It Works (booking process, FAQs, travel info, what to expect) Blog (updates, travel tips, inspiration) Contact Us (form, WhatsApp, phone, etc.)
Nice to have
• I want it to look professionla and be very user friendy to entice people to contact me to book boat trips
Should not have
• a store

```html
<!DOCTYPE html>
<html lang="en">
<head>
<meta charset="utf-8">
<title>Blue Keel Voyages – Website Pages</title>
<link rel="stylesheet" href="https://fonts.googleapis.com/css2?family=Oswald:wght@500&family=Poppins:wght@400;500;600&family=Josefin+Sans:wght@300&display=swap">
<style>
:root{
  --backdrop:#c9c9c9;
  --white:#ffffff;
  --navy:#0f4a6b;
  --navy-deep:#0c3a4c;
  --teal-title:#15607e;
  --sky:#46b1dc;
  --orange:#f0912c;
  --orange-soft:#f2a743;
  --blue-btn:#1d5ee6;
  --text:#5b6670;
  --line:#dde7ee;
  --field-line:#dfe7ec;
}
*{box-sizing:border-box;margin:0;padding:0}
html,body{width:1200px;height:1200px;overflow:hidden;background:var(--backdrop)}
body{font-family:"Poppins",Arial,sans-serif;color:var(--text)}
.stage{position:absolute;left:0;top:0;width:1932px;height:1932px;transform:scale(0.621118);transform-origin:0 0}
.page{position:absolute;background:var(--white);overflow:hidden}
.scaled{position:absolute;transform-origin:0 0}

/* header */
.site-header{position:absolute;left:0;top:0;width:509px;height:75px;background:var(--white)}
.brand{position:absolute;left:32px;top:9px;display:flex;flex-direction:column;align-items:center;gap:4px}
.brand-mark{width:24px;height:24px;border:2px solid var(--navy);border-radius:50%}
.brand-name{font-size:7px;line-height:8px;font-weight:600;color:var(--navy);text-transform:uppercase;text-align:center}
.header-cta{position:absolute;left:354px;top:20px;display:flex;gap:7px}
.btn{display:inline-flex;align-items:center;justify-content:center;height:17px;padding:0 10px;border-radius:9px;font-size:6px;font-weight:500;color:var(--white);letter-spacing:.2px}
.btn-orange{background:var(--orange)}
.btn-navy{background:var(--navy-deep)}
.main-nav{position:absolute;left:215px;top:46px;display:flex;gap:24px;font-size:5.8px;font-weight:500;color:var(--navy-deep)}
.main-nav i{font-style:normal;color:var(--orange);font-size:5px}
.main-nav .is-active{color:var(--navy)}

/* hero */
.hero{position:absolute;left:0;top:75px;width:509px;height:334px;overflow:hidden}
.hero-photo{position:absolute;inset:0;background:
  radial-gradient(ellipse 60% 18% at 30% 22%,rgba(255,255,255,.35),transparent 70%),
  radial-gradient(ellipse 50% 14% at 75% 38%,rgba(255,255,255,.3),transparent 70%),
  linear-gradient(180deg,#3f86b8 0%,#4f9bc9 22%,#8cc2dd 44%,#2c7bae 49%,#17659c 62%,#0e5487 80%,#0b4676 100%)}
.hero-title{position:absolute;left:44px;top:60px;font-family:"Oswald",Impact,sans-serif;font-weight:500;font-size:44px;line-height:52px;color:var(--white)}
.hero-sub{position:absolute;left:49px;top:118px;width:270px;font-size:8px;line-height:14px;color:var(--white)}
.hero-cta{position:absolute;left:47px;top:162px;height:26px;padding:0 10px;border-radius:13px;background:var(--orange);display:flex;align-items:center;gap:4px;font-size:7.5px;font-weight:600;color:var(--white)}
.hero-arrow{position:absolute;top:130px;width:18px;height:18px;border-radius:50%;display:flex;align-items:center;justify-content:center}
.hero-arrow.prev{left:4px;background:rgba(255,255,255,.25)}
.hero-arrow.next{left:481px;background:var(--white)}
.hero-dots{position:absolute;left:0;right:0;top:294px;display:flex;justify-content:center;gap:2px}
.hero-dots span{width:4px;height:4px;border-radius:50%;border:1px solid var(--white)}
.hero-dots span.on{background:var(--white)}

/* section titles */
.section-title{position:absolute;left:0;right:0;text-align:center;font-family:"Josefin Sans",Arial,sans-serif;font-weight:300;color:var(--teal-title);text-transform:uppercase;letter-spacing:.5px}
.divider{position:absolute;left:50%;width:60px;height:1px;margin-left:-30px;background:var(--line)}
.divider::after{content:"";position:absolute;left:28px;top:-1.5px;width:4px;height:4px;border-radius:50%;background:var(--orange)}

/* blog cards */
.post-card{position:absolute;width:143px;height:216px;background:var(--white);border-radius:8px;box-shadow:0 0 6px rgba(10,50,80,.16)}
.post-photo{position:absolute;left:3px;top:3px;right:3px;height:96px;border-radius:6px}
.post-meta{position:absolute;left:10px;top:116px;display:flex;gap:6px;font-size:4.6px;color:var(--navy)}
.post-meta b{display:inline-block;width:5px;height:5px;border-radius:1px;background:var(--orange-soft);margin-right:3px;vertical-align:-1px}
.post-meta em{display:inline-block;width:5px;height:5px;border-radius:50%;background:var(--orange);margin-right:3px;vertical-align:-1px}
.post-title{position:absolute;left:10px;top:129px;width:125px;font-size:7.2px;line-height:8.5px;font-weight:600;color:var(--navy)}
.post-excerpt{position:absolute;left:10px;width:122px;font-size:4.8px;line-height:9.5px;color:var(--text)}
.read-more{position:absolute;left:10px;top:183px;width:50px;height:12px;border-radius:6px;background:var(--blue-btn);color:var(--white);font-size:4.6px;font-weight:600;display:flex;align-items:center;justify-content:center}

/* inquiry form */
.inquiry{position:absolute;width:509px;height:342px}
.inquiry-bg{position:absolute;left:0;top:80px;width:509px;height:262px;background:
  radial-gradient(ellipse 30% 40% at 8% 80%,rgba(230,240,240,.8),transparent 70%),
  radial-gradient(ellipse 35% 30% at 92% 78%,rgba(20,40,50,.55),transparent 70%),
  linear-gradient(180deg,#ffffff 0%,#e9f6fb 18%,#bfe0ea 45%,#5ea9bf 75%,#1e6d8a 100%)}
.inquiry-panel{position:absolute;left:74px;top:80px;width:363px;height:220px;border-radius:14px;background:rgba(255,255,255,.45)}
.field{position:absolute;height:20px;background:var(--white);border:1px solid var(--field-line);font-size:6px;color:#444;padding:0 9px;display:flex;align-items:center;justify-content:space-between}
.field .caret{color:#9aa;font-size:5px}
.field .cal{width:5px;height:5px;background:#7fd3e8}
.field.message{align-items:flex-start;padding-top:6px;height:46px}
.submit{position:absolute;left:221px;top:273px;width:58px;height:17px;border-radius:9px;background:var(--orange);color:var(--white);font-size:6.5px;font-weight:500;display:flex;align-items:center;justify-content:center;gap:4px}

/* footer */
.site-footer{position:absolute;width:509px;height:180px;background:var(--navy-deep);color:var(--white)}
.footer-brand{position:absolute;left:30px;top:30px;display:flex;flex-direction:column;align-items:center;gap:10px}
.footer-brand .brand-mark{width:46px;height:46px;border:2px solid var(--white)}
.footer-brand .brand-name{font-size:10px;line-height:10px;font-weight:400;color:var(--white);letter-spacing:1px}
.footer-head{position:absolute;top:36px;font-size:7.5px;color:var(--sky);letter-spacing:.2px}
.footer-head::after{content:"";position:absolute;left:0;top:15px;width:22px;height:1px;background:rgba(255,255,255,.35)}
.footer-links{position:absolute;top:66px;list-style:none;font-size:5.4px;line-height:13.5px}
.footer-links li::before{content:"» ";color:var(--sky)}
.footer-contact{position:absolute;left:273px;display:flex;gap:8px;font-size:5px;line-height:6px}
.footer-contact .ico{width:10px;height:10px;border:1px solid rgba(255,255,255,.7);border-radius:2px;flex:none}
.news-input{position:absolute;left:390px;top:70px;width:90px;height:19px;background:#1f6f8f;font-size:4.5px;font-weight:600;display:flex;align-items:center;padding-left:8px}
.news-btn{position:absolute;left:390px;top:98px;width:71px;height:15px;background:var(--orange);font-size:4.8px;font-weight:600;display:flex;align-items:center;padding-left:8px}
.footer-rule{position:absolute;left:28px;top:148px;width:453px;height:1px;background:rgba(255,255,255,.18)}
.copyright{position:absolute;left:28px;top:158px;font-size:5px}
.socials{position:absolute;left:413px;top:154px;display:flex;gap:5px}
.socials span{width:12px;height:12px;border:1px solid rgba(255,255,255,.6);border-radius:2px}

/* article page */
.article-title{font-size:15px;line-height:19px}
.small-copy{position:absolute;font-size:4.3px;line-height:7.2px;color:#4b5660}
.article-frame{position:absolute;background:var(--white);border-radius:10px;box-shadow:0 0 6px rgba(10,50,80,.2);padding:5px}
.article-frame div{width:100%;height:100%;border-radius:7px}
.feature-title{position:absolute;font-size:7.3px;line-height:10.5px;font-weight:600;color:var(--navy)}
.feature-photo{position:absolute;border-radius:6px}
.faq{position:absolute;left:57px;top:873px;width:278px;height:200px;background:var(--white);border-radius:6px;box-shadow:0 0 5px rgba(10,50,80,.18)}
.faq-title{position:absolute;left:0;right:0;top:20px;text-align:center;font-size:9px;line-height:11px;font-weight:600;color:var(--navy)}
.faq-item{position:absolute;left:14px;width:252px}
.faq-item .num{position:absolute;left:0;top:1px;font-size:4.5px;font-weight:600;color:var(--navy)}
.faq-item .q{position:absolute;left:10px;top:0;font-size:5.8px;font-weight:500;color:var(--orange)}
.faq-item .a{position:absolute;left:10px;top:10px;width:240px;font-size:3.8px;line-height:6.5px;color:#4b5660}
.faq-rule{position:absolute;left:8px;width:262px;height:1px;background:var(--line)}

/* contact page */
.map-frame{position:absolute;left:62px;top:575px;width:436px;height:177px;background:var(--white);border-radius:12px;box-shadow:0 0 6px rgba(10,50,80,.2);padding:6px}
.map-area{width:100%;height:100%;border-radius:9px;background:linear-gradient(180deg,#8ed9f0 0%,#8ed9f0 52%,#a9dcc8 60%,#cfe8d8 100%)}
.contact-item{position:absolute;top:786px;display:flex;gap:10px;align-items:flex-start}
.contact-ico{width:21px;height:21px;border-radius:3px;background:var(--orange-soft);display:flex;align-items:center;justify-content:center;margin-top:3px}
.contact-item p{font-size:9px;line-height:10px;color:var(--navy-deep)}
</style>
</head>
<body>
<div class="stage">

<!-- ============ BLOG PAGE ============ -->
<div class="page" style="left:185px;top:179px;width:509px;height:1552px">
  <div class="scaled" style="left:0;top:0;width:509px;height:409px">
    <header class="site-header">
      <div class="brand"><span class="brand-mark"></span><span class="brand-name">Blue Keel<br>Voyages</span></div>
      <div class="header-cta"><span class="btn btn-orange">BOOK NOW</span><span class="btn btn-navy">CONTACT US</span></div>
      <nav class="main-nav"><span>SAILBOAT TRIPS <i>▾</i></span><span>BOATS &amp; PRICES <i>▾</i></span><span>HOW IT WORKS <i>▾</i></span><span class="is-active">BLOG</span></nav>
    </header>
    <section class="hero">
      <div class="hero-photo" role="img" aria-label="Catamarans anchored in open blue sea under a bright sky"></div>
      <h1 class="hero-title">San Blas Islands</h1>
      <p class="hero-sub">Panama Sailing Vacations.Ultimate Beaches &amp; Catamaran Tours</p>
      <span class="hero-cta">CHARTER INQUIRY FORM <svg width="8" height="8" viewBox="0 0 8 8"><path d="M1 4h5M4 2l2 2-2 2" stroke="#fff" fill="none" stroke-width="1"/></svg></span>
      <span class="hero-arrow prev"></span>
      <span class="hero-arrow next"><svg width="6" height="6" viewBox="0 0 6 6"><path d="M2 1l2 2-2 2" stroke="#0c3a4c" fill="none" stroke-width="1"/></svg></span>
      <div class="hero-dots"><span class="on"></span><span></span><span></span><span></span></div>
    </section>
  </div>

  <h2 class="section-title" style="top:453px;font-size:22px">Blog</h2>
  <div class="divider" style="top:486px"></div>

  <article class="post-card" style="left:29px;top:527px">
    <div class="post-photo" role="img" aria-label="Plates of seafood and salads on a table" style="background:linear-gradient(135deg,#b5645a,#d9a77e 45%,#8a3f3a)"></div>
    <div class="post-meta"><span><b></b>July 9, 2025</span><span><em></em>0 Comments</span></div>
    <h3 class="post-title">Diets On Board</h3>
    <p class="post-excerpt" style="top:142px">Dining &amp; Special Diets Onboard | BlueKeel-Voyages Dining &amp; Special Diets with BlueKeelVoyages Gourmet onboard meals</p>
    <span class="read-more">READ MORE</span>
  </article>
  <article class="post-card" style="left:183px;top:527px">
    <div class="post-photo" role="img" aria-label="Aerial view of a palm island with white beach" style="background:linear-gradient(135deg,#2f6a3a,#7fcfc7 50%,#2aa0b5)"></div>
    <div class="post-meta"><span><b></b>July 12, 2025</span><span><em></em>0 Comments</span></div>
    <h3 class="post-title">Luxury Catamaran Panama: The Ultimate San Blas Sailing Experience</h3>
    <p class="post-excerpt" style="top:160px">Luxury Catamaran Panama: The Ultimate San Blas Sailing Experience Dreaming of</p>
    <span class="read-more">READ MORE</span>
  </article>
  <article class="post-card" style="left:337px;top:527px">
    <div class="post-photo" role="img" aria-label="Catamaran sailing on turquoise water from above" style="background:linear-gradient(135deg,#0f6077,#2c98a8 55%,#0d5068)"></div>
    <div class="post-meta"><span><b></b>July 5, 2025</span><span><em></em>0 Comments</span></div>
    <h3 class="post-title">The Best Catamaran Tours In San Blas (2025 Guide)</h3>
    <p class="post-excerpt" style="top:151px">The Best Catamaran Tours in San Blas 2025 If you're dreaming of a tropical</p>
    <span class="read-more">READ MORE</span>
  </article>
  <article class="post-card" style="left:29px;top:770px">
    <div class="post-photo" role="img" aria-label="Catamaran beside a reef in clear blue water" style="background:linear-gradient(135deg,#0e5a78,#3aa6b8 55%,#0a4a66)"></div>
    <div class="post-meta"><span><b></b>July 5, 2025</span><span><em></em>0 Comments</span></div>
    <h3 class="post-title">Complete Guide To Sailing Vacations In Panama (2025)</h3>
    <p class="post-excerpt" style="top:151px">Complete Guide to Sailing Vacations in Panama Panama, the land where</p>
    <span class="read-more">READ MORE</span>
  </article>
  <article class="post-card" style="left:183px;top:770px">
    <div class="post-photo" role="img" aria-label="Sandy beach with palm trees and shallow clear water" style="background:linear-gradient(180deg,#4d7a3a,#d8cfa8 55%,#8fd2c6)"></div>
    <div class="post-meta"><span><b></b>March 6, 2025</span><span><em></em>0 Comments</span></div>
    <h3 class="post-title">Frequently Asked Questions About Sailing The San Blas Islands In 2025</h3>
    <p class="post-excerpt" style="top:160px">The San Blas Islands, located off the Caribbean coast of Panama</p>
    <span class="read-more">READ MORE</span>
  </article>

  <div class="scaled" style="left:0;top:1030px">
    <section class="inquiry">
      <h2 class="section-title" style="top:16px;font-size:22px">Charter Inquiry Form</h2>
      <div class="divider" style="top:50px"></div>
      <div class="inquiry-bg" role="img" aria-label="Aerial view of catamarans moored in turquoise water"></div>
      <div class="inquiry-panel"></div>
      <div class="field" style="left:102px;top:106px;width:97px">Name</div>
      <div class="field" style="left:207px;top:106px;width:97px">Email</div>
      <div class="field" style="left:311px;top:106px;width:97px">Mobile Number</div>
      <div class="field" style="left:102px;top:134px;width:306px">Select Your Charter <span class="caret">▾</span></div>
      <div class="field" style="left:102px;top:162px;width:97px">No.of Passengers <span class="caret">⇕</span></div>
      <div class="field" style="left:207px;top:162px;width:97px">Number of Days <span class="caret">⇕</span></div>
      <div class="field" style="left:311px;top:162px;width:97px">Date <span class="cal"></span></div>
      <div class="field" style="left:102px;top:189px;width:306px">What type of experience are you looking for? <span class="caret">▾</span></div>
      <div class="field message" style="left:102px;top:216px;width:306px">Message</div>
      <span class="submit">SUBMIT <svg width="7" height="7" viewBox="0 0 8 8"><path d="M1 4h5M4 2l2 2-2 2" stroke="#fff" fill="none"/></svg></span>
    </section>
  </div>

  <div class="scaled" style="left:0;top:1372px">
    <footer class="site-footer">
      <div class="footer-brand"><span class="brand-mark"></span><span class="brand-name">BLUE KEEL<br>VOYAGES</span></div>
      <h4 class="footer-head" style="left:135px">QUICK LINKS</h4>
      <ul class="footer-links" style="left:141px"><li>Fleet</li><li>About Us</li><li>Contact</li><li>Pricing</li><li>Guna Yala</li></ul>
      <ul class="footer-links" style="left:196px"><li>Itineraries</li><li>Activities</li><li>Blog</li><li>Languages</li><li>BOOK NOW</li></ul>
      <h4 class="footer-head" style="left:273px">CONTACT US</h4>
      <div class="footer-contact" style="top:68px"><span class="ico"></span><p>CALL US<br>0123 456 789</p></div>
      <div class="footer-contact" style="top:89px"><span class="ico"></span><p>EMAIL US<br>info@webname.com</p></div>
      <div class="footer-contact" style="top:110px"><span class="ico"></span><p>Address Line goes here,<br>Country Name, 4231</p></div>
      <h4 class="footer-head" style="left:389px">NEWSLETTER SIGN UP</h4>
      <div class="news-input">ENTER YOUR EMAIL</div>
      <div class="news-btn">SUBSCRIBE</div>
      <div class="footer-rule"></div>
      <p class="copyright">Copyright © 2025 All Rights Reserved By Company name</p>
      <div class="socials"><span></span><span></span><span></span><span></span></div>
    </footer>
  </div>
</div>

<!-- ============ ARTICLE PAGE ============ -->
<div class="page" style="left:738px;top:179px;width:392px;height:1552px">
  <div class="scaled" style="left:0;top:0;width:509px;height:409px;transform:scale(0.77)">
    <header class="site-header">
      <div class="brand"><span class="brand-mark"></span><span class="brand-name">Blue Keel<br>Voyages</span></div>
      <div class="header-cta"><span class="btn btn-orange">BOOK NOW</span><span class="btn btn-navy">CONTACT US</span></div>
      <nav class="main-nav"><span>SAILBOAT TRIPS <i>▾</i></span><span>BOATS &amp; PRICES <i>▾</i></span><span>HOW IT WORKS <i>▾</i></span><span class="is-active">BLOG</span></nav>
    </header>
    <section class="hero">
      <div class="hero-photo" role="img" aria-label="Catamarans anchored in open blue sea under a bright sky"></div>
      <h1 class="hero-title">San Blas Islands</h1>
      <p class="hero-sub">Panama Sailing Vacations.Ultimate Beaches &amp; Catamaran Tours</p>
      <span class="hero-cta">CHARTER INQUIRY FORM <svg width="8" height="8" viewBox="0 0 8 8"><path d="M1 4h5M4 2l2 2-2 2" stroke="#fff" fill="none" stroke-width="1"/></svg></span>
      <span class="hero-arrow prev"></span>
      <span class="hero-arrow next"><svg width="6" height="6" viewBox="0 0 6 6"><path d="M2 1l2 2-2 2" stroke="#0c3a4c" fill="none" stroke-width="1"/></svg></span>
      <div class="hero-dots"><span class="on"></span><span></span><span></span><span></span></div>
    </section>
  </div>

  <h2 class="section-title article-title" style="top:352px">Luxury Catamaran Panama:<br>The Ultimate San Blas Sailing Experience</h2>
  <p class="small-copy" style="left:46px;top:394px;width:300px;text-align:center">Dreaming of an unforgettable Panama sailing vacation? A luxury catamaran charter in San Blas offers unparalleled beauty, comfort, and privacy. Discover why these exclusive tours redefine the ultimate San Blas sailing trip, from pristine islands to personalized service.</p>
  <div class="article-frame" style="left:56px;top:430px;width:281px;height:155px"><div role="img" aria-label="White catamaran moored beside a palm-lined island" style="background:linear-gradient(180deg,#3f8fd0 0%,#7ab9e0 35%,#3f7a3a 50%,#e9eef2 62%,#2b8fbf 100%)"></div></div>

  <h3 class="feature-title" style="left:22px;top:619px;width:180px">Why Choose A Luxury Catamaran<br>In Panama For Your Vacation?</h3>
  <p class="small-copy" style="left:22px;top:655px;width:180px">Opting for a luxury catamaran in Panama elevates your travel experience beyond typical tours. These vessels offer spacious decks, private cabins, and gourmet dining, ensuring every moment of your San Blas sailing adventure is spent in absolute comfort and style. Ideal for families and couples seeking an exclusive escape.</p>
  <div class="feature-photo" role="img" aria-label="Warm wooden catamaran cabin with a made bed" style="left:220px;top:611px;width:148px;height:102px;background:linear-gradient(135deg,#6a3a1e,#d0893e 45%,#efe4d6 70%,#8a4b26)"></div>

  <div class="feature-photo" role="img" aria-label="Aerial view of a catamaran near a forested island beach" style="left:23px;top:732px;width:148px;height:102px;background:linear-gradient(135deg,#2e5d30,#5fa07a 40%,#e9e2c4 55%,#2f9fc0)"></div>
  <h3 class="feature-title" style="left:193px;top:739px;width:175px">Exploring The Pristine San Blas Islands<br>On A Luxury Charter</h3>
  <p class="small-copy" style="left:193px;top:771px;width:176px">Your luxury catamaran rental San Blas experience offers unparalleled access to over 365 untouched islands and cays. Each day brings new opportunities for snorkeling in vibrant coral reefs, relaxing on secluded white-sand beaches, and immersing yourself in the rich culture of the indigenous Guna people. It's more than a trip; it's a genuine San Blas sailing trip into paradise.</p>

  <div class="faq">
    <h3 class="faq-title">Your Questions About Luxury Catamaran<br>Tours In San Blas Answered</h3>
    <div class="faq-item" style="top:57px"><span class="num">01</span><span class="q">How To Get To San Blas Islands From Panama City?</span><p class="a">Getting to the San Blas Islands for your luxury catamaran tour from Panama City typically involves a 4x4 transfer followed by a short boat ride to your catamaran. Our team arranges all logistics for a seamless start to your San Blas adventure.</p></div>
    <div class="faq-rule" style="top:95px"></div>
    <div class="faq-item" style="top:104px"><span class="num">02</span><span class="q">San Blas Sailing Tour Reviews And Prices: What To Expect?</span><p class="a">Our luxury San Blas sailing tours consistently receive 5-star reviews for exceptional service, stunning destinations, and unforgettable experiences. Prices vary based on catamaran size, duration, and seasonality. Contact us for a personalized quote and to see detailed San Blas sailing tour reviews.</p></div>
    <div class="faq-rule" style="top:145px"></div>
    <div class="faq-item" style="top:155px"><span class="num">02</span><span class="q">Is An All-Inclusive San Blas Sailing Family Vacation An Option?</span><p class="a">Absolutely! Our all-inclusive San Blas sailing family vacations are designed for all ages. Enjoy child-friendly activities, customized menus, and a safe, comfortable environment aboard our spacious catamarans, making it the perfect family escape.</p></div>
  </div>
  <p class="small-copy" style="left:60px;top:1090px;width:272px;text-align:center">Tagged all-inclusive, catamaran charter, Guna Yala, luxury catamaran, Panama sailing, Panama tours, private tours, sailing vacation, San Blas Islands, travel guide</p>

  <div class="scaled" style="left:0;top:1151px;transform:scale(0.77)">
    <section class="inquiry">
      <h2 class="section-title" style="top:16px;font-size:22px">Charter Inquiry Form</h2>
      <div class="divider" style="top:50px"></div>
      <div class="inquiry-bg" role="img" aria-label="Aerial view of catamarans moored in turquoise water"></div>
      <div class="inquiry-panel"></div>
      <div class="field" style="left:102px;top:106px;width:97px">Name</div>
      <div class="field" style="left:207px;top:106px;width:97px">Email</div>
      <div class="field" style="left:311px;top:106px;width:97px">Mobile Number</div>
      <div class="field" style="left:102px;top:134px;width:306px">Select Your Charter <span class="caret">▾</span></div>
      <div class="field" style="left:102px;top:162px;width:97px">No.of Passengers <span class="caret">⇕</span></div>
      <div class="field" style="left:207px;top:162px;width:97px">Number of Days <span class="caret">⇕</span></div>
      <div class="field" style="left:311px;top:162px;width:97px">Date <span class="cal"></span></div>
      <div class="field" style="left:102px;top:189px;width:306px">What type of experience are you looking for? <span class="caret">▾</span></div>
      <div class="field message" style="left:102px;top:216px;width:306px">Message</div>
      <span class="submit">SUBMIT <svg width="7" height="7" viewBox="0 0 8 8"><path d="M1 4h5M4 2l2 2-2 2" stroke="#fff" fill="none"/></svg></span>
    </section>
  </div>

  <div class="scaled" style="left:0;top:1414px;transform:scale(0.77)">
    <footer class="site-footer">
      <div class="footer-brand"><span class="brand-mark"></span><span class="brand-name">BLUE KEEL<br>VOYAGES</span></div>
      <h4 class="footer-head" style="left:135px">QUICK LINKS</h4>
      <ul class="footer-links" style="left:141px"><li>Fleet</li><li>About Us</li><li>Contact</li><li>Pricing</li><li>Guna Yala</li></ul>
      <ul class="footer-links" style="left:196px"><li>Itineraries</li><li>Activities</li><li>Blog</li><li>Languages</li><li>BOOK NOW</li></ul>
      <h4 class="footer-head" style="left:273px">CONTACT US</h4>
      <div class="footer-contact" style="top:68px"><span class="ico"></span><p>CALL US<br>0123 456 789</p></div>
      <div class="footer-contact" style="top:89px"><span class="ico"></span><p>EMAIL US<br>info@webname.com</p></div>
      <div class="footer-contact" style="top:110px"><span class="ico"></span><p>Address Line goes here,<br>Country Name, 4231</p></div>
      <h4 class="footer-head" style="left:389px">NEWSLETTER SIGN UP</h4>
      <div class="news-input">ENTER YOUR EMAIL</div>
      <div class="news-btn">SUBSCRIBE</div>
      <div class="footer-rule"></div>
      <p class="copyright">Copyright © 2025 All Rights Reserved By Company name</p>
      <div class="socials"><span></span><span></span><span></span><span></span></div>
    </footer>
  </div>
</div>

<!-- ============ CONTACT PAGE ============ -->
<div class="page" style="left:1177px;top:179px;width:559px;height:1453px">
  <div class="scaled" style="left:0;top:0;width:509px;height:409px;transform:scale(1.098)">
    <header class="site-header">
      <div class="brand"><span class="brand-mark"></span><span class="brand-name">Blue Keel<br>Voyages</span></div>
      <div class="header-cta"><span class="btn btn-orange">BOOK NOW</span><span class="btn btn-navy">CONTACT US</span></div>
      <nav class="main-nav"><span>SAILBOAT TRIPS <i>▾</i></span><span>BOATS &amp; PRICES <i>▾</i></span><span>HOW IT WORKS <i>▾</i></span><span>BLOG</span></nav>
    </header>
    <section class="hero">
      <div class="hero-photo" role="img" aria-label="Catamarans anchored in open blue sea under a bright sky"></div>
      <h1 class="hero-title" style="top:66px">San Blas Islands</h1>
      <p class="hero-sub" style="top:124px">We Take Care Of Every Detail For You.</p>
      <span class="hero-cta" style="top:162px">CHARTER INQUIRY FORM <svg width="8" height="8" viewBox="0 0 8 8"><path d="M1 4h5M4 2l2 2-2 2" stroke="#fff" fill="none" stroke-width="1"/></svg></span>
      <span class="hero-arrow prev"></span>
      <span class="hero-arrow next"><svg width="6" height="6" viewBox="0 0 6 6"><path d="M2 1l2 2-2 2" stroke="#0c3a4c" fill="none" stroke-width="1"/></svg></span>
      <div class="hero-dots"><span class="on"></span><span></span><span></span><span></span></div>
    </section>
  </div>

  <h2 class="section-title" style="top:500px;font-size:24px">Contact Us</h2>
  <div class="divider" style="top:536px"></div>
  <div class="map-frame"><div class="map-area" role="img" aria-label="Map of the San Blas coast with the company location pin"></div></div>

  <div class="contact-item" style="left:45px">
    <span class="contact-ico"><svg width="11" height="11" viewBox="0 0 12 12"><path d="M3 1l2 2-1 2a6 6 0 0 0 3 3l2-1 2 2-1 2C5 11 1 7 1 2z" fill="none" stroke="#fff" stroke-width="1.1"/></svg></span>
    <p>CALL US<br>+507 6000 1234</p>
  </div>
  <div class="contact-item" style="left:188px">
    <span class="contact-ico"><svg width="11" height="11" viewBox="0 0 12 12"><rect x="1" y="3" width="10" height="7" fill="none" stroke="#fff"/><path d="M1 3l5 4 5-4" fill="none" stroke="#fff"/></svg></span>
    <p>MAIL US<br>hello@bluekeelvoyages.net</p>
  </div>
  <div class="contact-item" style="left:360px">
    <span class="contact-ico"><svg width="11" height="11" viewBox="0 0 12 12"><path d="M6 11S2 7 2 4.5a4 4 0 0 1 8 0C10 7 6 11 6 11z" fill="none" stroke="#fff"/><circle cx="6" cy="4.5" r="1.3" fill="#fff"/></svg></span>
    <p>Cayo Coral Anchorage,<br>San Blas Islands, Panama</p>
  </div>

  <div class="scaled" style="left:-10px;top:865px;transform:scale(1.14)">
    <section class="inquiry">
      <h2 class="section-title" style="top:16px;font-size:22px">Charter Inquiry Form</h2>
      <div class="divider" style="top:50px"></div>
      <div class="inquiry-bg" role="img" aria-label="Aerial view of catamarans moored in turquoise water"></div>
      <div class="inquiry-panel"></div>
      <div class="field" style="left:102px;top:106px;width:97px">Name</div>
      <div class="field" style="left:207px;top:106px;width:97px">Email</div>
      <div class="field" style="left:311px;top:106px;width:97px">Mobile Number</div>
      <div class="field" style="left:102px;top:134px;width:306px">Select Your Charter <span class="caret">▾</span></div>
      <div class="field" style="left:102px;top:162px;width:97px">No.of Passengers <span class="caret">⇕</span></div>
      <div class="field" style="left:207px;top:162px;width:97px">Number of Days <span class="caret">⇕</span></div>
      <div class="field" style="left:311px;top:162px;width:97px">Date <span class="cal"></span></div>
      <div class="field" style="left:102px;top:189px;width:306px">What type of experience are you looking for? <span class="caret">▾</span></div>
      <div class="field message" style="left:102px;top:216px;width:306px">Message</div>
      <span class="submit">SUBMIT <svg width="7" height="7" viewBox="0 0 8 8"><path d="M1 4h5M4 2l2 2-2 2" stroke="#fff" fill="none"/></svg></span>
    </section>
  </div>

  <div class="scaled" style="left:0;top:1257px;transform:scale(1.098)">
    <footer class="site-footer">
      <div class="footer-brand"><span class="brand-mark"></span><span class="brand-name">BLUE KEEL<br>VOYAGES</span></div>
      <h4 class="footer-head" style="left:135px">QUICK LINKS</h4>
      <ul class="footer-links" style="left:141px"><li>Fleet</li><li>About Us</li><li>Contact</li><li>Pricing</li><li>Guna Yala</li></ul>
      <ul class="footer-links" style="left:196px"><li>Itineraries</li><li>Activities</li><li>Blog</li><li>Languages</li><li>BOOK NOW</li></ul>
      <h4 class="footer-head" style="left:273px">CONTACT US</h4>
      <div class="footer-contact" style="top:68px"><span class="ico"></span><p>CALL US<br>+507 6000 1234</p></div>
      <div class="footer-contact" style="top:89px"><span class="ico"></span><p>EMAIL US<br>hello@bluekeelvoyages.net</p></div>
      <div class="footer-contact" style="top:110px"><span class="ico"></span><p>Address Line goes here,<br>Country Name, 4231</p></div>
      <h4 class="footer-head" style="left:389px">NEWSLETTER SIGN UP</h4>
      <div class="news-input">ENTER YOUR EMAIL</div>
      <div class="news-btn">SUBSCRIBE</div>
      <div class="footer-rule"></div>
      <p class="copyright">Copyright © 2025 All Rights Reserved By Company name</p>
      <div class="socials"><span></span><span></span><span></span><span></span></div>
    </footer>
  </div>
</div>

</div>
</body>
</html>
```